Heron Loan Partners Business Card

We need a business card design for our mortgage servicing company. In addition to servicing the loans of homeowners, we help homeowners with purchasing their homes and any mortgage refinancing. We would like to see designs that use the colors in the logo attached below (gold-ish yellow and navy blue), and any other design you deem fit! The design should communicate a simpler life with smart mortgages provided by Heron.

```html
<!DOCTYPE html>
<html lang="en">
<head>
<meta charset="utf-8">
<title>Heron Mortgage Business Card</title>
<link rel="stylesheet" href="https://fonts.googleapis.com/css2?family=Lato:wght@400;700&display=swap">
<style>
  :root {
    --backdrop: #2b2b2d;
    --card: #ffffff;
    --card-shade: #ececec;
    --gold: #d9a634;
    --navy: #23215a;
    --ink: #4a4a4f;
  }
  * { box-sizing: border-box; margin: 0; padding: 0; }
  html, body { width: 1200px; height: 900px; overflow: hidden; }
  body {
    background: var(--backdrop);
    font-family: "Lato", sans-serif;
    position: relative;
  }
  .card {
    position: absolute;
    left: 290px;
    width: 620px;
    height: 354px;
    background: linear-gradient(135deg, var(--card) 0%, var(--card) 55%, var(--card-shade) 100%);
    box-shadow: 0 10px 26px rgba(0,0,0,.45);
  }
  .card--front { top: 70px; }
  .card--back { top: 476px; }

  .brand {
    position: absolute;
    display: flex;
    align-items: center;
    gap: 12px;
    color: var(--navy);
    font-weight: 700;
    letter-spacing: .04em;
    white-space: nowrap;
  }
  .brand__dot {
    width: 14px; height: 14px; border-radius: 50%;
    background: var(--navy);
  }
  .card--front .brand { left: 50%; top: 50%; transform: translate(-50%, -50%); font-size: 40px; }
  .card--back .brand { left: 50%; top: 58px; transform: translateX(-50%); font-size: 32px; }

  .person {
    position: absolute;
    left: 0; right: 0; top: 150px;
    display: flex;
    align-items: center;
    padding: 0 40px;
    gap: 16px;
  }
  .person__rule { flex: 1; height: 1px; background: var(--gold); }
  .person__text { text-align: center; }
  .person__name {
    color: var(--gold);
    font-size: 22px;
    letter-spacing: .03em;
  }
  .person__role {
    color: var(--ink);
    font-size: 14px;
    margin-top: 2px;
  }

  .contact {
    position: absolute;
    bottom: 34px;
    display: flex;
    flex-direction: column;
    gap: 8px;
    font-size: 14px;
    color: var(--ink);
  }
  .contact--left { left: 40px; }
  .contact--right { right: 40px; align-items: flex-end; }
  .contact__item { display: flex; align-items: center; gap: 8px; white-space: nowrap; }
  .contact__icon { width: 14px; height: 14px; flex: none; }
</style>
</head>
<body>

<section class="card card--front" aria-label="Card front">
  <div class="brand"><span class="brand__dot"></span>Heron Mortgage</div>
</section>

<section class="card card--back" aria-label="Card back">
  <div class="brand"><span class="brand__dot"></span>Heron Mortgage</div>

  <div class="person">
    <span class="person__rule"></span>
    <div class="person__text">
      <div class="person__name">DANIEL PRICE</div>
      <div class="person__role">Director</div>
    </div>
    <span class="person__rule"></span>
  </div>

  <div class="contact contact--left">
    <div class="contact__item">
      <svg class="contact__icon" viewBox="0 0 16 16" aria-hidden="true">
        <path fill="var(--navy)" d="M3.5 1.5l2.5 2.8-1.4 1.8c.9 2 2.4 3.5 4.4 4.4l1.8-1.4 2.8 2.5-1.6 2.1C7 13.4 2.6 9 1.4 3.1z"/>
      </svg>
      <span>415-555-0142</span>
    </div>
    <div class="contact__item">
      <svg class="contact__icon" viewBox="0 0 16 16" aria-hidden="true">
        <path fill="var(--navy)" d="M8 1a5 5 0 0 0-5 5c0 3.6 5 9 5 9s5-5.4 5-9a5 5 0 0 0-5-5zm0 7a2 2 0 1 1 0-4 2 2 0 0 1 0 4z"/>
      </svg>
      <span>24 Harbor Lane, Bayview 1200</span>
    </div>
  </div>

  <div class="contact contact--right">
    <div class="contact__item">
      <span>info@heronmortgage.com</span>
      <svg class="contact__icon" viewBox="0 0 16 16" aria-hidden="true">
        <rect x="1" y="3" width="14" height="10" fill="var(--navy)"/>
        <path d="M1.5 3.5L8 9l6.5-5.5" fill="none" stroke="#fff" stroke-width="1.2"/>
      </svg>
    </div>
    <div class="contact__item">
      <span>www.heronmortgage.com</span>
      <svg class="contact__icon" viewBox="0 0 16 16" aria-hidden="true">
        <g fill="none" stroke="var(--navy)" stroke-width="1.2">
          <circle cx="8" cy="8" r="6.5"/>
          <ellipse cx="8" cy="8" rx="3" ry="6.5"/>
          <path d="M1.5 8h13M2.5 4.7h11M2.5 11.3h11"/>
        </g>
      </svg>
    </div>
  </div>
</section>

</body>
</html>
```